Business Card Design

Need a new business card to represent our legal vertical focus. attached is an example of our old business card and newest logo. we would like the card to also identify "Legal Tech" as a tag line of business.

Our new address is
4817 Marlowe Hatchfield Rd.
Suite 518
Cincinnati, OH 45917

we no longer have a fax number.

Target Market(s)

Tech Consulting for Law Firms

Industry/Entity Type

Legal

Contact Information for Business Card

should use logo and colors. we are a b2b company

Font styles to use
Other font styles liked:
• tahoma

Requirements
Must have
• all print should be in lower case just as shown in photos. tag line should not
Should not have
• pinstripes or drop shadows

```html
<!DOCTYPE html>
<html lang="en">
<head>
<meta charset="utf-8">
<title>StrandLink Legal Tech – Business Card</title>
<link rel="stylesheet" href="https://fonts.googleapis.com/css2?family=Open+Sans:wght@400;600;700&display=swap">
<style>
  :root {
    --backdrop: #d9d9d7;
    --card-black: #000000;
    --strip-black: #121212;
    --brand-orange: #ec4e23;
    --brand-blue: #2e3d8f;
    --text-white: #ffffff;
    --tagline-grey: #8a8a8a;
  }
  * { box-sizing: border-box; margin: 0; padding: 0; }
  html, body {
    width: 1200px; height: 900px; overflow: hidden;
    background: var(--backdrop);
    font-family: "Open Sans", Tahoma, sans-serif;
  }
  .canvas { position: relative; width: 1200px; height: 900px; }
  .card {
    position: absolute; left: 250px; width: 700px; height: 400px;
    background: var(--card-black); overflow: hidden;
  }
  .card--front { top: 40px; }
  .card--back { top: 470px; }

  .card-bands { position: absolute; left: 0; right: 0; bottom: 0; }
  .band-blue { height: 8px; background: var(--brand-blue); }
  .band-orange { height: 56px; background: var(--brand-orange); }

  .brand { position: absolute; }
  .brand-name { font-weight: 700; letter-spacing: -1px; line-height: 1; }
  .brand-tagline {
    font-weight: 400; letter-spacing: 18px; line-height: 1;
    margin-top: 6px; margin-left: 14px;
  }
  .card--front .brand { left: 190px; top: 112px; }
  .card--front .brand-name { font-size: 70px; color: var(--text-white); }
  .card--front .brand-tagline { font-size: 22px; color: var(--text-white); }

  .card--back .brand { left: 60px; top: 88px; z-index: 2; }
  .card--back .brand-name { font-size: 60px; color: var(--brand-orange); }
  .card--back .brand-tagline { font-size: 20px; color: var(--tagline-grey); }

  .contact-strip {
    position: absolute; left: 0; right: 0; top: 195px; bottom: 64px;
    background: var(--strip-black);
  }
  .person { position: absolute; right: 50px; top: 100px; text-align: left; }
  .person-name { color: var(--brand-orange); font-weight: 700; font-size: 20px; }
  .person-role { color: var(--text-white); font-size: 17px; margin-top: 2px; }

  .contact-group {
    position: absolute; color: var(--text-white);
    font-size: 15px; line-height: 1.6; white-space: nowrap;
  }
  .contact-group--address { left: 50px; top: 218px; }
  .contact-group--phone { left: 320px; top: 262px; }
  .contact-group--online { left: 470px; top: 280px; }
  .contact-line { display: flex; align-items: center; gap: 7px; }
  .contact-line .icon { width: 13px; height: 13px; fill: var(--brand-orange); flex: none; }
</style>
</head>
<body>
<main class="canvas">

  <section class="card card--front" aria-label="Business card front">
    <div class="brand">
      <div class="brand-name">StrandLink</div>
      <div class="brand-tagline">Legal Tech</div>
    </div>
    <div class="card-bands">
      <div class="band-blue"></div>
      <div class="band-orange"></div>
    </div>
  </section>

  <section class="card card--back" aria-label="Business card back">
    <div class="contact-strip"></div>

    <div class="brand">
      <div class="brand-name">StrandLink</div>
      <div class="brand-tagline">Legal Tech</div>
    </div>

    <div class="person">
      <div class="person-name">marcus hale</div>
      <div class="person-role">managing director</div>
    </div>

    <div class="contact-group contact-group--address">
      <div class="contact-line">
        <svg class="icon" viewBox="0 0 12 12" aria-hidden="true"><path d="M6 0a4 4 0 0 0-4 4c0 3 4 8 4 8s4-5 4-8a4 4 0 0 0-4-4zm0 5.6A1.6 1.6 0 1 1 6 2.4a1.6 1.6 0 0 1 0 3.2z"/></svg>
        <span>4817 marlowe hatchfield rd.,</span>
      </div>
      <div class="contact-line"><span>suite 518,</span></div>
      <div class="contact-line"><span>cincinnati, oh 45917</span></div>
    </div>

    <div class="contact-group contact-group--phone">
      <div class="contact-line">
        <svg class="icon" viewBox="0 0 12 12" aria-hidden="true"><path d="M1 3.5C1 2 3 1 6 1s5 1 5 2.5V5H8.5V3.8h-5V5H1zM2 6h8l1 5H1z"/></svg>
        <span>123.456.7890</span>
      </div>
    </div>

    <div class="contact-group contact-group--online">
      <div class="contact-line">
        <svg class="icon" viewBox="0 0 12 12" aria-hidden="true"><path d="M0 2h12v8H0zm1 1v.4l5 3.3 5-3.3V3z"/></svg>
        <span>info@youremail.com</span>
      </div>
      <div class="contact-line">
        <svg class="icon" viewBox="0 0 12 12" aria-hidden="true"><path d="M5 7 7 5M4.2 5.8 2.6 7.4a1.8 1.8 0 0 0 2.5 2.5l1.6-1.6M7.8 6.2l1.6-1.6a1.8 1.8 0 0 0-2.5-2.5L5.3 3.7" stroke="#ec4e23" stroke-width="1.4" fill="none" stroke-linecap="round"/></svg>
        <span>www.website.com</span>
      </div>
    </div>

    <div class="card-bands">
      <div class="band-blue"></div>
      <div class="band-orange"></div>
    </div>
  </section>

</main>
</body>
</html>
```